Harborlight Amusement Collective (HAC)

We need a business card design for Harborlight Amusement Collective. Modern and sleek looking, with all critical information. Open to single or double sided designs, if double sided info needs to be all on one side. The main Logo is Harborlight Amusement collective and must be on the card. The other three logos are for the brands that fall under the group, they might be good on the back.

Industry/Entity Type

Business

```html
<!DOCTYPE html>
<html lang="en">
<head>
<meta charset="utf-8">
<title>Harborlight Amusement Collective — Business Card</title>
<link rel="stylesheet" href="https://fonts.googleapis.com/css2?family=Montserrat:wght@400;500;600;800&family=Roboto+Condensed:wght@700&display=swap">
<style>
  :root {
    --bg: #d9d9d9;
    --card: #ffffff;
    --blue: #2056a3;
    --green: #86a53a;
    --ink: #1f1f1f;
    --muted: #555555;
    --faint: #f0f1f3;
  }
  * { box-sizing: border-box; margin: 0; padding: 0; }
  html, body { width: 1200px; height: 852px; overflow: hidden; }
  body {
    background: var(--bg);
    font-family: "Montserrat", sans-serif;
    position: relative;
  }
  .card {
    position: absolute;
    top: 276px;
    width: 525px;
    height: 300px;
    background: var(--card);
    border-radius: 18px;
    overflow: hidden;
    box-shadow: 0 6px 14px rgba(0,0,0,.18);
  }
  .card--brands { left: 60px; }
  .card--contact { left: 615px; }

  /* Wordmark */
  .wordmark {
    display: flex;
    align-items: center;
    gap: 10px;
    color: var(--blue);
    font-weight: 800;
    text-transform: uppercase;
    letter-spacing: .02em;
    line-height: 1.05;
  }
  .wordmark__square { width: 34px; height: 34px; background: var(--blue); flex: none; }

  /* Brands side */
  .card--brands .wordmark {
    position: absolute; top: 52px; left: 0; right: 0;
    justify-content: center; font-size: 21px;
  }
  .rule { position: absolute; height: 1px; background: var(--green); }
  .rule--top { top: 118px; left: 60px; right: 60px; }
  .rule--bottom { top: 240px; left: 30px; right: 30px; }
  .brands__label {
    position: absolute; top: 128px; left: 0; right: 0;
    text-align: center; font-size: 13px; color: var(--muted);
  }
  .brands {
    position: absolute; top: 160px; left: 20px; right: 20px;
    display: flex; justify-content: space-around; align-items: center;
  }
  .brand {
    display: flex; align-items: center; gap: 6px;
    font-size: 17px; font-weight: 600; color: var(--blue);
  }
  .brand__dot { width: 14px; height: 14px; border-radius: 50%; background: var(--green); }
  .brand-divider { width: 1px; height: 36px; background: #b8b8b8; }
  .brands__url {
    position: absolute; top: 256px; left: 0; right: 0;
    text-align: center; font-size: 13px; color: var(--blue); font-weight: 500;
  }

  /* Contact side */
  .card--contact .wordmark {
    position: absolute; top: 34px; left: 28px; font-size: 19px;
  }
  .decor {
    position: absolute; top: 40px; right: 30px;
    width: 170px; height: 170px; background: var(--faint);
  }
  .contact {
    position: absolute; top: 108px; left: 300px; width: 200px;
    font-size: 12.5px; color: var(--ink); line-height: 1.45;
  }
  .contact__address { margin-bottom: 6px; }
  .contact__line { display: flex; align-items: center; gap: 8px; white-space: nowrap; }
  .contact__line svg { width: 12px; height: 12px; fill: var(--ink); flex: none; }
  .panel {
    position: absolute; right: 0; bottom: 0;
    width: 290px; height: 86px;
    background: var(--blue);
    border-top-left-radius: 26px;
  }
  .panel__url {
    position: absolute; top: 22px; left: 44px;
    color: #fff; font-size: 13px;
  }
  .band {
    position: absolute; left: 0; bottom: 0;
    width: 240px; height: 12px; background: var(--green);
  }
  .person { position: absolute; left: 34px; top: 214px; }
  .person__name {
    font-family: "Roboto Condensed", sans-serif;
    font-weight: 700; font-size: 24px; color: var(--blue);
  }
  .person__role { font-size: 13px; color: var(--ink); }
</style>
</head>
<body>

<section class="card card--brands">
  <div class="wordmark">
    <span class="wordmark__square"></span>
    <span>Harborlight Amusement<br>Collective</span>
  </div>
  <div class="rule rule--top"></div>
  <p class="brands__label">Our Brands</p>
  <div class="brands">
    <div class="brand"><span class="brand__dot"></span>HarborTix</div>
    <span class="brand-divider"></span>
    <div class="brand">Bleacherline Hosting</div>
    <span class="brand-divider"></span>
    <div class="brand">gatepass</div>
  </div>
  <div class="rule rule--bottom"></div>
  <p class="brands__url">www.harborlightamusement.com</p>
</section>

<section class="card card--contact">
  <div class="decor"></div>
  <div class="wordmark">
    <span class="wordmark__square"></span>
    <span>Harborlight Amusement<br>Collective</span>
  </div>
  <div class="contact">
    <p class="contact__address">88 Quayside Row, Port<br>Merrin, US 40217</p>
    <p class="contact__line">
      <svg viewBox="0 0 24 24" aria-hidden="true"><path d="M6.6 10.8a15 15 0 0 0 6.6 6.6l2.2-2.2c.3-.3.7-.4 1-.2 1.1.4 2.3.6 3.6.6.6 0 1 .4 1 1V20c0 .6-.4 1-1 1A17 17 0 0 1 3 4c0-.6.4-1 1-1h3.5c.6 0 1 .4 1 1 0 1.3.2 2.5.6 3.6.1.3 0 .7-.2 1z"/></svg>
      555.014.2290
    </p>
    <p class="contact__line">
      <svg viewBox="0 0 24 24" aria-hidden="true"><path d="M2 5h20v14H2zm2 2v.5l8 5 8-5V7l-8 5z"/></svg>
      jordan@harborlight.com
    </p>
  </div>
  <div class="panel"><p class="panel__url">www.harborlightamusement.com</p></div>
  <div class="band"></div>
  <div class="person">
    <p class="person__name">Jordan Lee Avery</p>
    <p class="person__role">Managing Director</p>
  </div>
</section>

</body>
</html>
```